Looking for a dynamic business card for a pizzeria.

A business card with our food, logo, and space for name, title, email, website, phone. The card should convey quality, unique, amazing. On the front, I envision food photo or photos with the owners names and contact information. On the back, more food with locations, website, facebook, twitter, instagram icons. It should look polished, not cartoonish, or plain.
Target Market(s)
upscale, local food buyers, 30-50 years in age.
Industry/Entity Type
Restaurant
Contact Information for Business Card
Business Name: Bru'nettix, LLC
Website: www.brunettix.com
Back:
2 locations: (can list on the back of card)
1. Eastbrook
4087 Corlan Avenue
Larkport, WA 98310
360-481-5067
2. Ridgeview
7315 Wendmere Road
Larkport, WA 98314
360-293-8840
front:
EDITABLE space for
Business name
Person's Name
title
2nd title
Email address
cell-phone number
Requirements
Must have
- logo
- my food photo or photos (no watermarks showing)
- locations on back
- Person contact information on front
- full bleed

```html
<!DOCTYPE html>
<html lang="en">
<head>
<meta charset="utf-8">
<title>Bru'nettix, LLC – Business Card</title>
<link href="https://fonts.googleapis.com/css2?family=Open+Sans:wght@400;600;700&display=swap" rel="stylesheet">
<style>
  :root {
    --stage: #ece8e2;
    --green-dark: #123d1c;
    --green: #1f5a2c;
    --green-light: #2d6e3a;
    --white: #ffffff;
    --red: #b3202a;
    --photo-warm: #c98a3a;
    --photo-crust: #a86a2a;
    --photo-leaf: #5e8a3a;
    --photo-light: #e8d7bf;
    --shadow: rgba(0, 0, 0, 0.28);
  }
  * { box-sizing: border-box; margin: 0; padding: 0; }
  html, body {
    width: 1200px; height: 913px; overflow: hidden;
    background: var(--stage);
    font-family: "Open Sans", Arial, sans-serif;
  }
  .canvas { position: relative; width: 1200px; height: 913px; }

  .card {
    position: absolute;
    width: 540px; height: 310px;
    border-radius: 16px;
    overflow: hidden;
    box-shadow: 0 14px 30px var(--shadow);
    color: var(--white);
  }

  /* Front */
  .card-front {
    left: 60px; top: 100px;
    background: linear-gradient(135deg, var(--green-light) 0%, var(--green) 45%, var(--green-dark) 100%);
  }
  .brand {
    position: absolute; left: 40px; top: 38px;
    display: flex; align-items: center; gap: 12px;
  }
  .brand-name { font-size: 34px; font-weight: 400; letter-spacing: 1px; white-space: nowrap; }
  .brand-dot { width: 44px; height: 44px; border-radius: 50%; background: var(--white); }
  .company {
    position: absolute; left: 40px; top: 98px;
    font-size: 22px; font-weight: 700; letter-spacing: 0.5px;
  }
  .rule {
    position: absolute; left: 40px; right: 0; top: 134px;
    height: 1px; background: rgba(255,255,255,0.75);
  }
  .flag {
    position: absolute; left: 0; top: 150px;
    width: 32px; height: 40px; display: flex; flex-direction: column;
  }
  .flag span { flex: 1; }
  .flag .f-white { background: var(--white); }
  .flag .f-red { background: var(--red); }
  .person { position: absolute; left: 48px; top: 146px; }
  .person-name { font-size: 22px; font-weight: 700; letter-spacing: 0.5px; line-height: 1.1; }
  .person-title { font-size: 13px; font-weight: 400; opacity: 0.9; }
  .contact-list {
    position: absolute; left: 48px; top: 214px;
    list-style: none; font-size: 14px; line-height: 24px;
  }
  .contact-list li { display: flex; align-items: center; gap: 9px; }
  .contact-list svg { width: 12px; height: 12px; fill: none; stroke: var(--white); stroke-width: 1.6; }

  /* Back */
  .card-back { left: 600px; top: 500px; }
  .food-photo {
    position: absolute; inset: 0;
    background:
      radial-gradient(ellipse 55% 40% at 62% 38%, var(--photo-warm), transparent 70%),
      radial-gradient(ellipse 40% 25% at 55% 55%, var(--photo-leaf), transparent 75%),
      radial-gradient(ellipse 35% 30% at 25% 70%, var(--photo-crust), transparent 75%),
      linear-gradient(135deg, var(--photo-light) 0%, #c7a27a 50%, #8a5a2e 100%);
  }
  .location {
    position: absolute; font-size: 15px; font-weight: 600; line-height: 20px;
    white-space: nowrap;
    text-shadow: 0 1px 3px rgba(0,0,0,0.5);
  }
  .location-one { left: 32px; top: 176px; }
  .location-two { left: 300px; top: 96px; }
  .back-brand {
    position: absolute; left: 32px; bottom: 22px;
    display: flex; align-items: center; gap: 10px;
    background: var(--white); padding: 6px 12px; border-radius: 4px;
  }
  .back-brand .brand-name { font-size: 22px; color: var(--green-dark); }
  .back-brand .brand-dot { width: 26px; height: 26px; background: var(--red); }
</style>
</head>
<body>
<main class="canvas">

  <section class="card card-front" aria-label="Business card front">
    <div class="brand">
      <span class="brand-name">Bru'nettix</span>
      <span class="brand-dot"></span>
    </div>
    <div class="company">BRU'NETTIX, LLC</div>
    <div class="rule"></div>
    <div class="flag"><span class="f-white"></span><span class="f-red"></span><span class="f-white"></span></div>
    <div class="person">
      <div class="person-name">MARCO DELANE</div>
      <div class="person-title">Director, President</div>
    </div>
    <ul class="contact-list">
      <li><svg viewBox="0 0 12 12"><path d="M2 1.5l2 0 1 2.5-1.3 1a6 6 0 0 0 3.3 3.3l1-1.3 2.5 1v2c0 .5-.5 1-1 1A9 9 0 0 1 1 2.5c0-.5.5-1 1-1z"/></svg>360-518-2274</li>
      <li><svg viewBox="0 0 12 12"><rect x="1" y="2.5" width="10" height="7"/><path d="M1 2.5l5 4 5-4"/></svg>info@marcodelane.com</li>
      <li><svg viewBox="0 0 12 12"><circle cx="6" cy="6" r="5"/><path d="M1 6h10M6 1c-2.5 3-2.5 7 0 10M6 1c2.5 3 2.5 7 0 10"/></svg>www.brunettix.com</li>
    </ul>
  </section>

  <section class="card card-back" aria-label="Business card back">
    <div class="food-photo" role="img" aria-label="Photo of a toasted grilled sandwich with greens and tomato"></div>
    <div class="location location-two">
      360-293-8840<br>Ridgeview 7315 Wendmere<br>Road Larkport, WA 98314
    </div>
    <div class="location location-one">
      360-481-5067<br>Eastbrook 4087 Corlan<br>Avenue Larkport, WA 98310
    </div>
    <div class="back-brand">
      <span class="brand-name">Bru'nettix</span>
      <span class="brand-dot"></span>
    </div>
  </section>

</main>
</body>
</html>
```